Classy, Elegant, Simple Business Card Design

Looking to have a classy, simple, and elegant design. Want a top notch designed business card. I really like the look of the new torvane credit card. I also like the design I attached. I am trying to reach 21-29 year old females for booking us for there wedding or event. We offer Disc Jockey Service, Photo Booth Rentals, and Uplighting .

Target Market(s)

21-28 year old females

Contact Information for Business Card

Has to have logo, website, email, and phone number

Font styles to use
Other font styles liked:
• open to font choice, modern, clean
Designer to choose
33a6d7
0791cd
0555a3
ffffff

Requirements
Must have
• Has to have logo, website, email, and phone number
Nice to have
• I really like the design of the new torvane credit card. I also included my logo and some designs I like
Should not have
• clutter or too much info

```html
<!DOCTYPE html>
<html lang="en">
<head>
<meta charset="utf-8">
<title>Tidelight Event Group – Business Card</title>
<link href="https://fonts.googleapis.com/css2?family=Work+Sans:wght@400;500;600&display=swap" rel="stylesheet">
<style>
  :root {
    --navy: #142f57;
    --deep-blue: #0555a3;
    --bright-blue: #0791cd;
    --sky-blue: #33a6d7;
    --white: #ffffff;
    --ink: #3a3f47;
    --grey: #8a8f96;
    --backdrop: #e9ecf0;
  }
  * { margin: 0; padding: 0; box-sizing: border-box; }
  html, body {
    width: 1200px; height: 912px; overflow: hidden;
    background: var(--backdrop);
    font-family: "Work Sans", Arial, sans-serif;
  }
  .canvas { position: relative; width: 1200px; height: 912px; }

  .card {
    position: absolute;
    width: 580px; height: 331px;
    border-radius: 18px;
    overflow: hidden;
    box-shadow: 0 10px 28px rgba(20, 30, 50, 0.18);
  }

  /* Front: navy */
  .card-front {
    left: 60px; top: 90px;
    background: var(--navy);
    color: var(--white);
    display: flex; flex-direction: column; align-items: center;
  }
  .card-front .brand { margin-top: 108px; }
  .card-front .website {
    position: absolute; bottom: 40px; left: 0; right: 0;
    text-align: center; font-size: 15px; letter-spacing: 1.5px;
  }

  .brand { display: flex; align-items: center; gap: 12px; }
  .brand-dot {
    width: 18px; height: 18px; border-radius: 50%;
    background: var(--sky-blue);
  }
  .brand-name {
    font-weight: 500; font-size: 38px; letter-spacing: 3px;
    color: var(--sky-blue); line-height: 1;
  }
  .brand-sub {
    margin-top: 10px; font-size: 13px; letter-spacing: 8px;
    color: var(--grey); text-align: center;
  }

  /* Back: white with details */
  .card-back {
    left: 560px; top: 490px;
    background: var(--white);
  }
  .card-back .brand-block {
    position: absolute; left: 42px; top: 128px;
  }
  .card-back .brand-name { font-size: 34px; color: var(--bright-blue); }
  .card-back .brand-sub { text-align: left; padding-left: 32px; }

  .details {
    position: absolute; left: 318px; top: 36px; width: 232px;
    color: var(--ink);
  }
  .person-name {
    font-weight: 600; font-size: 21px; color: var(--bright-blue);
    letter-spacing: 0.5px;
  }
  .person-role { font-size: 13px; margin-top: 2px; }
  .rule { height: 1px; background: var(--bright-blue); margin: 14px 0; }
  .address { font-size: 13px; line-height: 1.45; }
  .contact-list { list-style: none; font-size: 13px; line-height: 1.7; }
  .contact-list li { display: flex; align-items: center; gap: 8px; }
  .contact-list svg { width: 11px; height: 11px; flex: none; }
  .contact-list .accent { color: var(--deep-blue); font-weight: 500; }

  .base-band {
    position: absolute; left: 0; bottom: 0; width: 580px; height: 14px;
  }
</style>
</head>
<body>
<main class="canvas">

  <section class="card card-front" aria-label="Card front">
    <div class="brand">
      <span class="brand-dot"></span>
      <span class="brand-name">TIDELIGHT</span>
    </div>
    <div class="brand-sub">EVENT GROUP</div>
    <p class="website">www.tidelight.com</p>
  </section>

  <section class="card card-back" aria-label="Card back">
    <div class="brand-block">
      <div class="brand">
        <span class="brand-dot"></span>
        <span class="brand-name">TIDELIGHT</span>
      </div>
      <div class="brand-sub">EVENT GROUP</div>
    </div>

    <div class="details">
      <h1 class="person-name">DANIEL REYES</h1>
      <p class="person-role">Managing Partner</p>
      <div class="rule"></div>
      <p class="address">418 W Harlow Ave.,<br>Pasadena, CA 91103</p>
      <div class="rule"></div>
      <ul class="contact-list">
        <li>
          <svg viewBox="0 0 12 12" aria-hidden="true"><path d="M2.5 1h2l1 2.5-1.3 1a6 6 0 0 0 3.3 3.3l1-1.3L11 7.5v2A1.5 1.5 0 0 1 9.5 11 8.5 8.5 0 0 1 1 2.5 1.5 1.5 0 0 1 2.5 1z" fill="var(--bright-blue)"/></svg>
          555-214-7730
        </li>
        <li>
          <svg viewBox="0 0 12 12" aria-hidden="true"><rect x="1" y="2.5" width="10" height="7" fill="none" stroke="var(--bright-blue)" stroke-width="1.2"/><path d="M1 2.5l5 4 5-4" fill="none" stroke="var(--bright-blue)" stroke-width="1.2"/></svg>
          info@tidelight.com
        </li>
        <li>
          <svg viewBox="0 0 12 12" aria-hidden="true"><circle cx="6" cy="6" r="5" fill="none" stroke="var(--bright-blue)" stroke-width="1.1"/><ellipse cx="6" cy="6" rx="2.2" ry="5" fill="none" stroke="var(--bright-blue)" stroke-width="1"/><path d="M1 6h10" stroke="var(--bright-blue)" stroke-width="1"/></svg>
          <span>www.<span class="accent">tidelight</span>.com</span>
        </li>
      </ul>
    </div>

    <svg class="base-band" viewBox="0 0 580 14" preserveAspectRatio="none" aria-hidden="true">
      <rect x="0" y="0" width="580" height="14" fill="var(--navy)"/>
      <polygon points="330,0 580,0 580,14 322,14" fill="var(--bright-blue)"/>
    </svg>
  </section>

</main>
</body>
</html>
```